WP website design (Tarnwick)

We need a wordpress design for an established auction and real estate company based in Arkansas. The winning design will incorporate a professional color scheme with company logo in a clean layout. The design needs to consider that this will be developed on a responsive theme.

Industry/Entity Type

Real Estate

Font styles to use
Sans Serif

Colors

Designer to choose colors to be used in the design.

Requirements
Must have
• Site will have slideshow, please use stock real estate or other image. A rough idea of homepage content is attached - not necessarily for design purposes.

Navigation Structure is:
1) Home
2) Auctions
3) Services
4) For Sale
5) About Us
6) Ned Videos
7) News & Events
8) Contact Us

Widgets will include:
Social media icons (Facebook, Youtube, RSS)
Testimonials Widget - this should be prominent
Featured Video
Email Signup form (Sign up to receive exclusive email updates for Tarnwick auctions. )
Nice to have
• A drop down menu example
Should not have
• no gavel in the design

```html
<!DOCTYPE html>
<html lang="en">
<head>
<meta charset="utf-8">
<title>Tarnwick Auction &amp; Marketing</title>
<link href="https://fonts.googleapis.com/css2?family=Arimo:wght@400;700&display=swap" rel="stylesheet">
<style>
:root{
  --green:#0b7a36;
  --green-dark:#086a2d;
  --text:#7a7a7a;
  --nav-text:#555;
  --rule:#d8d8d8;
  --arrow:#b9b9b9;
  --white:#fff;
}
*{box-sizing:border-box;margin:0;padding:0}
html,body{width:1025px;height:1200px;overflow:hidden;background:var(--white)}
body{position:relative;font-family:"Arimo",Arial,sans-serif;color:var(--text)}
.abs{position:absolute}
a{color:inherit;text-decoration:none}

/* header */
.brand{left:156px;top:38px}
.brand-name{display:block;font-size:31px;line-height:32px;color:#1a1a1a;letter-spacing:.5px}
.brand-sub{display:block;font-size:11px;color:var(--green);letter-spacing:.6px;margin:2px 0 0 9px;text-transform:uppercase}
.social{left:668px;top:52px;display:flex;gap:6px}
.social span{width:20px;height:20px;border-radius:50%;background:#9a9a9a;display:block}
.phone{left:760px;top:54px;display:flex;align-items:center;gap:6px;color:var(--green);font-size:13px}

/* nav */
.main-nav{left:155px;top:98px;width:717px;height:40px;border-top:2px solid #e6e6e6;background:linear-gradient(#f1f1f1,#fff 60%)}
.main-nav ul{list-style:none;display:flex;justify-content:space-between;padding:15px 32px 0 28px;font-size:10.5px;color:var(--nav-text)}

/* slider */
.hero{left:155px;top:138px;width:716px;height:306px;background:linear-gradient(180deg,#1d3a8c 0%,#3b5aa8 30%,#8a7a52 62%,#4b4a2e 80%,#2c8ad0 100%)}
.hero-caption{left:155px;top:358px;width:375px;height:72px;background:rgba(20,20,20,.8);color:var(--white);padding:14px 0 0 17px}
.hero-caption h1{font-weight:400;font-size:17.5px}
.hero-caption p{font-size:13px;margin-top:8px}
.pager{display:flex;gap:1px}
.pager span{width:14px;height:14px;background:var(--arrow);display:flex;align-items:center;justify-content:center}
.hero-caption .pager{position:absolute;right:4px;top:4px}
.hero-caption .pager span{background:#555}

/* testimonial */
.testimonial-photo{left:154px;top:461px;width:107px;height:107px;border:1px solid #ccc;padding:2px;background:var(--white)}
.testimonial-photo div{width:100%;height:100%;background:linear-gradient(160deg,#cfd9e0,#7aa8cf)}
.testimonial{left:286px;top:469px;width:562px}
.testimonial h2{font-weight:400;font-size:10.5px;color:var(--green)}
.testimonial p{font-size:8.8px;line-height:16px;margin-top:9px}
.testimonial .author{font-size:12px;color:var(--green);margin-top:8px}

/* featured video */
.section-title{font-weight:400;font-size:13px;color:var(--green)}
.video{left:154px;top:618px;width:220px;height:132px;border:1px solid #ccc}
.video-frame{height:120px;background:linear-gradient(160deg,#b9c7d2,#e6dcd0 55%,#9db5c9)}
.video-bar{height:11px;background:#eee;border-top:1px solid #ccc;display:flex;align-items:center;gap:4px;padding:0 4px;font-size:5px;color:#222}
.video-bar .track{flex:1;height:2px;background:#999}
.video-text{left:393px;top:615px;width:230px;font-size:8.8px;line-height:16px}

/* email signup */
.signup{left:646px;top:614px;width:226px;height:126px;background:var(--green);color:var(--white);padding:14px 0 0 21px}
.signup h2{font-weight:400;font-size:13px}
.signup p{font-size:7.4px;margin-top:8px}
.signup .field{margin:8px 0 0 -2px;width:193px;height:20px;background:var(--white);border:1px solid #cfcfcf;font-size:7.2px;color:#666;padding:6px 10px}
.signup .btn{position:absolute;left:123px;top:86px;width:90px;height:22px;border-radius:3px;background:linear-gradient(#fff,#e4e4e4);color:var(--green);font-size:10px;display:flex;align-items:center;justify-content:center}

/* listings */
.listing{top:805px;width:226px}
.listing-img{height:135px}
.listing h3{font-weight:400;font-size:12px;color:var(--green);margin-top:15px}
.listing p{font-size:8.8px;line-height:16px;margin-top:4px}
.listing .meta{font-size:8.8px;line-height:16px;margin-top:4px}
.listing .meta b{font-weight:400;color:var(--green)}
.listing .btn{display:inline-flex;align-items:center;justify-content:center;width:103px;height:27px;margin-top:6px;background:var(--green);border-radius:2px;color:var(--white);font-size:8.6px}

/* footer */
.footer{left:155px;top:1125px;width:717px;border-top:2px solid var(--rule);display:flex;justify-content:space-between;padding:22px 2px 0 3px;font-size:7.6px;color:#666}
.footer nav span{margin:0 7px}
</style>
</head>
<body>

<header>
  <div class="abs brand"><span class="brand-name">TARNWICK</span><span class="brand-sub">Auction &amp; Marketing, LLC</span></div>
  <div class="abs social" aria-label="Social links"><span></span><span></span><span></span></div>
  <div class="abs phone">
    <svg width="20" height="20" viewBox="0 0 20 20" aria-hidden="true"><path d="M4 2c1 0 2 3 2 4s-2 1-1 3 3 4 5 5 2-1 3-1 4 1 4 2-1 3-3 3C8 18 2 12 2 4c0-1 1-2 2-2z" fill="#8a8a8a"/></svg>
    <span>1-800-555-0147</span>
  </div>
</header>

<nav class="abs main-nav">
  <ul><li>Home</li><li>Auctions</li><li>Services</li><li>For Sale</li><li>About Us</li><li>Ned Videos</li><li>News &amp; Events</li><li>Contact Us</li></ul>
</nav>

<section>
  <div class="abs hero" role="img" aria-label="Large two-storey home at dusk with lit windows and a backyard pool"></div>
  <div class="abs hero-caption">
    <h1>Tarnwick Auction &amp; Marketing</h1>
    <p>It is a long established fact that a reader will be distracted</p>
    <div class="pager"><span><svg width="6" height="8"><path d="M5 1 1 4l4 3" stroke="#aaa" fill="none"/></svg></span><span><svg width="6" height="8"><path d="M1 1l4 3-4 3" stroke="#aaa" fill="none"/></svg></span></div>
  </div>
</section>

<section>
  <div class="abs testimonial-photo"><div role="img" aria-label="Portrait of a smiling client in a light blue shirt"></div></div>
  <div class="abs testimonial">
    <h2>It is a long established fact that a reader will be distracted by the readable content</h2>
    <p>It is a long established fact that a reader will be distracted by the readable content of a page when looking at its layout. The point of using Lorem Ipsum is that it has a more-or-less normal distribution of letters, as opposed to using 'Content here, content here', making it look like readable English. Many desktop publishing packages and web page editors...</p>
    <div class="author">Morgan Hale</div>
  </div>
  <div class="abs pager" style="left:842px;top:462px"><span><svg width="6" height="8"><path d="M5 1 1 4l4 3" stroke="#fff" fill="none"/></svg></span><span><svg width="6" height="8"><path d="M1 1l4 3-4 3" stroke="#fff" fill="none"/></svg></span></div>
</section>

<section>
  <h2 class="abs section-title" style="left:154px;top:590px">Featured Video</h2>
  <div class="abs video">
    <div class="video-frame" role="img" aria-label="Family of four sitting together outdoors"></div>
    <div class="video-bar"><span>▶</span><span>00:00</span><span class="track"></span><span>00:00</span></div>
  </div>
  <div class="abs video-text">
    <p>It is a long established fact that a reader will be distracted by the readable content of a page when looking at its layout. The point of using Lorem Ipsum is that it has a more-or-less normal distribution of letters, as opposed to using 'Content here, content here.</p>
    <p style="margin-top:16px">it look like readable English. Many desktop publishing packages and web page editors...</p>
  </div>
  <form class="abs signup">
    <h2>Email Signup</h2>
    <p>Get our recent updates through your email id :</p>
    <div class="field">Enter your Email id :</div>
    <div class="btn">Subscribe</div>
  </form>
</section>

<section>
  <h2 class="abs section-title" style="left:154px;top:776px">Current Actions</h2>
  <div class="abs pager" style="left:842px;top:776px"><span><svg width="6" height="8"><path d="M5 1 1 4l4 3" stroke="#fff" fill="none"/></svg></span><span><svg width="6" height="8"><path d="M1 1l4 3-4 3" stroke="#fff" fill="none"/></svg></span></div>

  <article class="abs listing" style="left:154px">
    <div class="listing-img" role="img" aria-label="Farmhouse with wraparound porch on a green lawn" style="background:linear-gradient(#9ec3e6,#dfe9ef 45%,#7fa04a 70%,#6f9a3a)"></div>
    <h3>Real Estate</h3>
    <p>It is a long established fact that a reader will be distracted by the readable content of a page when looking at its layout. The point of using...</p>
    <div class="meta">Name : <b>Morgan Hale</b><br>Location : <b>Canada</b>, Sq.ft : <b>2300</b>,</div>
    <a class="btn">View more details</a>
  </article>
  <article class="abs listing" style="left:401px">
    <div class="listing-img" role="img" aria-label="Smiling couple meeting with an agent" style="background:linear-gradient(135deg,#e8dcc8,#c9b79f 45%,#7fa3c9)"></div>
    <h3>Real Estate</h3>
    <p>It is a long established fact that a reader will be distracted by the readable content of a page when looking at its layout. The point of using...</p>
    <div class="meta">Name : <b>Morgan Hale</b><br>Location : <b>Canada</b>, Sq.ft : <b>2300</b>,</div>
    <a class="btn">View more details</a>
  </article>
  <article class="abs listing" style="left:646px">
    <div class="listing-img" role="img" aria-label="Row of cream townhouses with grey roofs" style="background:linear-gradient(#8fb3d8,#d9dde0 40%,#e6dcb8 70%,#8a8f86)"></div>
    <h3>Real Estate</h3>
    <p>It is a long established fact that a reader will be distracted by the readable content of a page when looking at its layout. The point of using...</p>
    <div class="meta">Name : <b>Morgan Hale</b><br>Location : <b>Canada</b>, Sq.ft : <b>2300</b>,</div>
    <a class="btn">View more details</a>
  </article>
</section>

<footer class="abs footer">
  <nav>Home<span>|</span>Auctions<span>|</span>Services<span>|</span>For Sale<span>|</span>About Us<span>|</span>Ned Videos<span>|</span>News &amp; Events<span>|</span>Contact Us</nav>
  <div>© Copyrights 2014. Tarnwick. All rights reserved.</div>
</footer>

</body>
</html>
```